Sophisticated, clean website reflecting my feminine, playful side to sell my abstract art,

I need a website no more than 3 pages to showcase my paintings, a little about me and some contact info. I do abstracts so looking for something a little edgy, yet feminine and current.
Updates

Hi there, These are some artists websites that I Iike: Marnelvoss.com (I like how airy it is) peterwallombry.com garethpolvens.com (I like how it scrolls) I'll need a place for a photo ( a headshot-i do not have it yet so I'll need to be able to upload that later) as well as an area for my bio. Also, it's important that I will be able to upload any new photos and descriptions easily so it should be user friendly. Lastly, I like in a sunny place so would like to have this seem upbeat and playful as that is how i like to paint. thanks-I'm trying to upload my photos now -

Target Market(s)

ppl ages 35-70 who want large scale art for their homes

Industry/Entity Type

art

Coding

Coded - Design and coding required

Number of Pages Required

3 page

Colors

Designer to choose colors to be used in the design.

Requirements
Must have
• photos of my art, a place for my bio, be easy to reach me. tasteful-nothing too "in your face" -my clients are pretty high end and organized. They like clean lines
Nice to have
• sophisticated background, muted tones in the back-similar clean font throughout-no cursive
Should not have
• too many dark areas. Too many blocks of color. Too serious.

```html
<!DOCTYPE html>
<html lang="en">
<head>
<meta charset="utf-8">
<title>Lena Marlowe — Abstract Art</title>
<link rel="stylesheet" href="https://fonts.googleapis.com/css2?family=Cinzel:wght@400&family=Quicksand:wght@400;500&display=swap">
<style>
  :root {
    --ink: #3a3a3a;
    --ink-soft: #4a4a4a;
    --rule: #9a9a9a;
    --arrow: #6f6f6f;
    --bg-top: #ffffff;
    --bg-bottom: #e9e4e0;
    --frame: #b9b9b9;
    --hero-a: #c9869a;
    --hero-b: #a4563c;
    --hero-c: #d8b2b8;
    --art-a: #e9eef2;
    --art-b: #d4a64a;
    --art-c: #3f66a8;
    --portrait: #f4f4f4;
  }
  * { box-sizing: border-box; margin: 0; padding: 0; }
  html, body { width: 1200px; height: 2926px; overflow: hidden; }
  body {
    position: relative;
    font-family: "Quicksand", sans-serif;
    color: var(--ink);
    background: linear-gradient(to bottom, var(--bg-top) 0, var(--bg-top) 860px, var(--bg-bottom) 2926px);
  }
  .abs { position: absolute; }

  .site-header { left: 0; top: 0; width: 1200px; height: 113px; background: var(--bg-top); border-bottom: 1.5px solid var(--rule); }
  .brand { left: 0; width: 1200px; top: 24px; text-align: center; font-size: 55px; font-weight: 400; letter-spacing: 1px; color: var(--ink-soft); line-height: 64px; }
  .brand-mark { display: inline-block; width: 30px; height: 44px; background: #bdbdbd; vertical-align: -3px; margin: 0 14px; }

  .main-nav { left: 0; top: 113px; width: 1200px; height: 58px; background: var(--bg-top); }
  .main-nav a { position: absolute; top: 18px; transform: translateX(-50%); font-size: 17px; color: var(--ink); text-decoration: none; letter-spacing: 0.3px; }

  .hero { left: 0; top: 171px; width: 1200px; height: 682px;
    background: radial-gradient(circle at 55% 50%, var(--hero-b) 0, var(--hero-a) 30%, var(--hero-c) 60%, var(--hero-b) 100%); }
  .chev { position: absolute; }

  .section-title { left: 0; width: 1200px; text-align: center; font-family: "Cinzel", serif; font-size: 50px; font-weight: 400; color: var(--ink-soft); letter-spacing: 2px; line-height: 56px; }
  .title-rule { height: 2px; background: var(--rule); }

  .portrait { left: 104px; top: 1087px; width: 317px; height: 341px; border: 1.5px solid var(--frame); border-radius: 10px; background: var(--portrait); }
  .bio { left: 472px; top: 1085px; width: 635px; font-size: 18px; letter-spacing: -0.35px; line-height: 31px; text-align: justify; color: var(--ink); }
  .bio p + p { margin-top: 14px; }

  .artwork { left: 204px; top: 1705px; width: 808px; height: 529px; border: 1.5px solid var(--frame); border-radius: 10px;
    background: linear-gradient(135deg, var(--art-b) 0%, var(--art-a) 35%, var(--art-c) 60%, var(--art-a) 80%, var(--art-b) 100%); }

  .contact-lead { left: 0; width: 1200px; top: 2488px; text-align: center; font-size: 21px; }
  .contact-item { left: 0; width: 1200px; text-align: center; font-size: 17px; line-height: 24px; }
  .contact-item svg { vertical-align: -6px; margin-right: 8px; }
  .footer-note { left: 0; width: 1200px; top: 2864px; text-align: center; font-size: 15px; }
</style>
</head>
<body>
  <header class="abs site-header">
    <div class="abs brand">LENA<span class="brand-mark"></span>MARLOWE</div>
  </header>
  <nav class="abs main-nav">
    <a style="left:302px">HOME</a>
    <a style="left:490px">ABOUT ME</a>
    <a style="left:689px">GALLERY</a>
    <a style="left:885px">CONTACT</a>
  </nav>

  <div class="abs hero" role="img" aria-label="Abstract painting of a rose in pink, rust and dark brushstrokes">
    <svg class="chev" style="left:22px;top:452px" width="26" height="46" viewBox="0 0 26 46"><polyline points="23,3 3,23 23,43" fill="none" stroke="#fff" stroke-width="3"/></svg>
    <svg class="chev" style="left:1137px;top:452px" width="26" height="46" viewBox="0 0 26 46"><polyline points="3,3 23,23 3,43" fill="none" stroke="#fff" stroke-width="3"/></svg>
  </div>

  <h2 class="abs section-title" style="top:968px">ABOUT ME</h2>
  <div class="abs title-rule" style="left:474px;top:1030px;width:260px"></div>
  <div class="abs portrait" role="img" aria-label="Artist headshot placeholder"></div>
  <div class="abs bio">
    <p>Lorem ipsum dolor sit amet, consectetur adipiscing elit, sed do eiusmod tempor incididunt ut labore et dolore magna aliqua. Ut enim ad minim veniam, quis nostrud exercitation Lorem ipsum dolor sit amet, consectetur adipiscing elit, sed do eiusmod tempor incididunt ut labore et dolore</p>
    <p>Duis aute irure dolor in reprehenderit in voluptate velit esse cillum dolore eu fugiat nulla pariatur. Excepteur sint occaecat cupidatat non proident, sunt in culpa qui officia deserunt mollit anim id est laborum.</p>
    <p>Sed ut perspiciatis unde pariatur. Excepteur sint occaecat cupidatat non proident, sunt in culpa qui officia deserunt mollit anim id est laborum.didunt ut labore et dolore Duis aute irure dolor in reprehenderit in voluptate</p>
  </div>

  <h2 class="abs section-title" style="top:1590px">GALLERY</h2>
  <div class="abs title-rule" style="left:508px;top:1647px;width:181px"></div>
  <svg class="abs" style="left:122px;top:1930px" width="28" height="46" viewBox="0 0 28 46"><polyline points="25,3 4,23 25,43" fill="none" stroke="var(--arrow)" stroke-width="3.5"/></svg>
  <div class="abs artwork" role="img" aria-label="Abstract painting with swirls of ochre, rust and cobalt blue on white"></div>
  <svg class="abs" style="left:1060px;top:1930px" width="28" height="46" viewBox="0 0 28 46"><polyline points="3,3 24,23 3,43" fill="none" stroke="var(--arrow)" stroke-width="3.5"/></svg>

  <h2 class="abs section-title" style="top:2377px">CONTACT ME</h2>
  <div class="abs title-rule" style="left:459px;top:2438px;width:317px"></div>
  <p class="abs contact-lead">Please get in touch with me on below details.</p>

  <p class="abs contact-item" style="top:2570px">
    <svg width="28" height="22" viewBox="0 0 28 22"><rect x="1" y="1" width="26" height="20" fill="none" stroke="var(--ink)" stroke-width="1.3"/><polyline points="1,1 14,12 27,1" fill="none" stroke="var(--ink)" stroke-width="1.3"/></svg>info@lenamarlowe.com</p>
  <p class="abs contact-item" style="top:2621px">
    <svg width="28" height="28" viewBox="0 0 28 28"><path d="M6 3 L10 3 L12 9 L9 11 C10 15 13 18 17 19 L19 16 L25 18 L25 22 C25 24 23 25 21 25 C12 24 4 16 3 7 C3 5 4 3 6 3 Z" fill="none" stroke="var(--ink)" stroke-width="1.3"/></svg>Phone: (123) 555 0142</p>
  <p class="abs contact-item" style="top:2670px">
    <svg width="26" height="26" viewBox="0 0 26 26"><circle cx="13" cy="13" r="11.5" fill="none" stroke="var(--ink)" stroke-width="1.3"/></svg>snapfolio @lmarloweart</p>
  <p class="abs contact-item" style="top:2722px">
    <svg width="26" height="26" viewBox="0 0 26 26"><rect x="2" y="2" width="22" height="22" fill="none" stroke="var(--ink)" stroke-width="1.3"/></svg>reelio @lmpainter</p>

  <p class="abs footer-note">© 2022 Lena Marlowe&nbsp;&nbsp; All Rights Reserved</p>
</body>
</html>
```